A Techincal Author needs a site to promote his Programming Books

The StudyAlong series is a collection of books focusing on building the same app with different technologies. The purpose of this project is to design a web site home page that can be used to sell the books.

Expected Deliverables
• StudyAlong Logo as Illustrator file
• Master graphic design files for any relevant web assets
• HTML and CSS for home page, if applicable

Target Market(s)

The target market for our series is web programmers. They are people who have some experience, but want to learn a new tool. Programmers are analytical, logical people who like structure in the things they do.

Here are some things our customers like:

• Chirply / Postbox
• Crown of Ashes / Hollow Tide / Salt Hollow
• SmartPhones, Tablets, Stridelets, and other tech gadgets.

The design should try to speak to that market.

Requirements
Must have
• The primary tasks for this project are:
• 1) Create "Study Along" Logo.
• * All “NetPivot” properties use a similar logo approach, with the NetPivot ball icon on the left, a reflection below it. The company name is on the right, roughly the same size as the ball icon. A tag line underneath the company name, roughly the same size as the reflection.
• * Company Name: Study Along
• * Tagline: Knowledge to Boost Your Career
• * Logo color is up to the discretion of the designer, but should be compatible with the site design.
• * Sample Logos for other NetPivot properties in Illustrator format are available as attachments to this project.
• 2) Design the Study Along Home Page.
• The home page should follow this format:
• * Logo
• * Nav Bar
• • Buy (The Home Page)
• • About
• • Contact
• * Main Content
• • Home page content detailed in attachment
• * Footer
• • Copyright notice
• • Links to other stuff we do ( net-pivot.example | marlonpeake.example | BeyondTheGrid.example )
Nice to have
• It would be nice to have a book as part of the home page content.
Should not have
• Please do not use the same color scheme as BeyondTheGrid.example or Plumvane.example or QueryTheMaven.example

```html
<!DOCTYPE html>
<html lang="en">
<head>
<meta charset="utf-8">
<title>Study Along – Knowledge to Boost Your Career</title>
<link href="https://fonts.googleapis.com/css2?family=Raleway:wght@400;500;600;700&family=Open+Sans:ital,wght@0,400;0,600;0,700;1,400&display=swap" rel="stylesheet">
<style>
:root{
  --red:#e0313e;
  --amber:#f6a710;
  --ink:#333;
  --muted:#777;
  --topbar:#e4e4e4;
  --row-a:#f3f3f3;
  --row-b:#e9e9e9;
  --blue:#1f4fb8;
  --white:#fff;
}
*{box-sizing:border-box;margin:0;padding:0}
html,body{width:742px;height:1200px;overflow:hidden;background:var(--white)}
body{position:relative;font-family:"Raleway",sans-serif;color:var(--ink)}
.abs{position:absolute}

.topbar{left:0;top:0;width:742px;height:19px;background:var(--topbar)}
.topbar .call{position:absolute;right:49px;top:4px;font:italic 9px "Open Sans",sans-serif;color:#444}

.brand{left:52px;top:78px;display:flex;align-items:center;gap:8px}
.brand .mark{width:18px;height:18px;background:var(--red)}
.brand .name{font:700 13px "Open Sans",sans-serif;color:var(--red);letter-spacing:.5px;white-space:nowrap}

.search{left:499px;top:60px;width:199px;height:21px;border-radius:4px;background:#f1f1f1}
.search span{position:absolute;left:9px;top:4px;font:italic 9px "Open Sans",sans-serif;color:#aaa}
.search svg{position:absolute;right:5px;top:3px}

.nav{left:0;top:110px;width:742px;height:34px;background:var(--red);display:flex;align-items:center;padding-left:53px}
.nav a{color:var(--white);text-decoration:none;font:500 11px "Raleway",sans-serif;margin-right:28px;white-space:nowrap}

.hero{left:0;top:144px;width:742px;height:262px;background:linear-gradient(100deg,#5a3a2c 0%,#b98a6a 30%,#d9b59b 50%,#8a5a40 75%,#3a2418 100%)}
.hero h1{position:absolute;left:50px;top:72px;font:600 29px "Raleway",sans-serif;line-height:33px;color:var(--white);white-space:nowrap}
.hero h1 em{font-style:normal;color:var(--amber)}

.signup{left:422px;top:173px;width:230px;height:208px;background:rgba(246,167,16,.93);padding:6px}
.signup .frame{width:100%;height:100%;border:1px solid rgba(255,255,255,.55);padding:20px 21px 0}
.signup h2{font:500 19px "Raleway",sans-serif;color:var(--white);text-align:center;line-height:23px;margin-bottom:10px;letter-spacing:.5px;white-space:nowrap}
.signup .field{height:25px;background:#fafafa;border:1px solid #ddd;margin-bottom:7px;font:9px "Open Sans",sans-serif;color:#999;padding:6px 10px}
.signup .submit{height:34px;border:2px solid var(--white);margin-top:4px;font:600 15px "Raleway",sans-serif;color:var(--white);text-align:center;line-height:30px;letter-spacing:1px}

.section-title{left:0;width:742px;text-align:center;font:400 18px "Raleway",sans-serif;color:#333}
.section-title::after{content:"";display:block;width:93px;height:1px;background:#999;margin:7px auto 0}

.welcome-copy{left:20px;top:468px;width:702px;text-align:center;font:400 9px "Raleway",sans-serif;line-height:17px;color:var(--muted);white-space:nowrap}

.tab{top:635px;width:163px;height:34px;background:var(--red);color:var(--white);font:500 12px "Raleway",sans-serif;text-align:center;line-height:34px;white-space:nowrap}
.tab.active::after{content:"";position:absolute;left:74px;bottom:-7px;border:7px solid transparent;border-top-color:var(--red);border-bottom:0}

.table{left:48px;top:680px;width:654px;height:171px;border:1px solid #ddd;padding:2px}
.row{display:flex;height:41.5px;margin-bottom:.5px}
.row:nth-child(odd){background:var(--row-a)}
.row:nth-child(even){background:var(--row-b)}
.row > div{display:flex;align-items:center;border-right:2px solid var(--white);font:400 9.5px "Raleway",sans-serif;color:#555;white-space:nowrap}
.c-name{width:145px;padding-left:15px}
.c-price{width:78px;justify-content:center}
.c-buy{width:110px;justify-content:center}
.c-store{flex:1;border-right:0!important;padding-left:29px}
.buy-btn{width:79px;height:20px;border-radius:10px;background:var(--blue);border:1px solid #0d2c7a;color:var(--white);font:600 8px "Open Sans",sans-serif;text-align:center;line-height:18px}
.store-btn{width:97px;height:28px;background:var(--amber);border-radius:2px;color:var(--white);display:flex;flex-direction:column;justify-content:center;padding-left:11px;overflow:hidden}
.store-btn small{font:400 6.5px/8px "Open Sans",sans-serif}
.store-btn b{font:600 12px/13px "Open Sans",sans-serif}

.updates{left:0;top:875px;width:742px;height:219px;background:var(--red)}
.updates h3{position:absolute;left:0;top:18px;width:742px;text-align:center;font:500 18px "Raleway",sans-serif;color:var(--white)}
.updates h3::after{content:"";display:block;width:153px;height:1px;background:var(--white);margin:7px auto 0}
.updates .field{position:absolute;left:256px;width:232px;height:32px;background:var(--white);font:9px "Open Sans",sans-serif;color:#555;padding:11px}
.updates .go{position:absolute;left:331px;top:156px;width:93px;height:32px;background:#111;color:var(--white);font:700 9px "Open Sans",sans-serif;text-align:center;line-height:32px}

.partners-label{left:42px;top:1117px;font:9px "Open Sans",sans-serif;color:#222}
.partner-badge{left:41px;top:1131px;width:196px;height:40px;border:1px solid #ccc;background:#f4f6fa}
.partner-badge span{position:absolute;left:10px;top:9px;width:174px;height:20px;background:#c9d3e6;border-radius:3px}
.copyright{right:55px;top:1128px;font:9px "Open Sans",sans-serif;color:#333;white-space:nowrap}
.social{right:55px;top:1155px;display:flex;gap:12px}
.social i{width:8px;height:8px;border-radius:50%;background:#888;display:block}
</style>
</head>
<body>

<div class="abs topbar"><span class="call">Call us&nbsp; 1-800-555-0199</span></div>

<div class="abs brand"><span class="mark"></span><span class="name">STUDY ALONG</span></div>

<div class="abs search">
  <span>search product</span>
  <svg width="15" height="15" viewBox="0 0 15 15"><circle cx="6" cy="6" r="4.8" fill="none" stroke="#555" stroke-width="1.2"/><line x1="9.5" y1="9.5" x2="13.5" y2="13.5" stroke="#555" stroke-width="1.3"/></svg>
</div>

<nav class="abs nav">
  <a>HOME</a><a>ABOUT US</a><a>OUR PRODUCTS</a><a>SUPPORT</a><a>DOWNLOAD</a><a>CONTACT US</a>
</nav>

<section class="abs hero" role="img" aria-label="Photo of hands holding a tablet computer">
  <h1>KNOWLEDGE TO BOOST<br><em>YOUR CAREER</em></h1>
</section>

<form class="abs signup">
  <div class="frame">
    <h2>SIGN UP FOR<br>A FREE SAMPLE</h2>
    <div class="field">First Name</div>
    <div class="field">Email Address</div>
    <div class="submit">SUBMIT</div>
  </div>
</form>

<h2 class="abs section-title" style="top:427px">Welcome to Study Along</h2>
<p class="abs welcome-copy">Lorem ipsum dolor sit amet, consectetuer adipiscing elit. Aenean commodo ligula eget dolor. Aenean massa. Cum sociis&nbsp; natoque penatibus et magnis<br>Lorem ipsum dolor sit amet, consectetuer adipiscing elit. Aenean commodo ligula eget&nbsp; dolor. Aenean massa. Cum sociis natoque<br>penatibus et magnisdolor sit amet, consectetuer adipiscing elit&nbsp;&nbsp; Aenean commodo ligula eget dolor. Aenean massa. Cum socii<br>natoque penatibus et magnis dolor sit amet consectetuer adipiscing elit.Aenean commodo ligula eget dolor. Aenean massa.<br>Cum sociis natoque penatibus et magnis .</p>

<h2 class="abs section-title" style="top:582px">Our Products</h2>

<div class="abs tab active" style="left:48px">Angulon 1.5 &amp; Strapkit</div>
<div class="abs tab" style="left:222px">Angulon 2 &amp; Strapkit</div>
<div class="abs tab" style="left:397px">Reactor</div>

<div class="abs table">
  <div class="row"><div class="c-name">With Mock Services</div><div class="c-price">$5.99</div><div class="c-buy"><span class="buy-btn">BUY FROM US</span></div><div class="c-store"><span class="store-btn"><small>Buy from</small><b>Shopvale</b></span></div></div>
  <div class="row"><div class="c-name">With Nodeline Services</div><div class="c-price">$5.99</div><div class="c-buy"><span class="buy-btn">BUY FROM US</span></div><div class="c-store"><span class="store-btn"><small>Buy from</small><b>Shopvale</b></span></div></div>
  <div class="row"><div class="c-name">With Frostfuse Services</div><div class="c-price">$5.99</div><div class="c-buy"><span class="buy-btn">BUY FROM US</span></div><div class="c-store"><span class="store-btn"><small>Buy from</small><b>Shopvale</b></span></div></div>
  <div class="row"><div class="c-name">Buy Them All</div><div class="c-price">$9.99</div><div class="c-buy"><span class="buy-btn">BUY FROM US</span></div><div class="c-store"><span class="store-btn"><small>Buy from</small><b>Shopvale</b></span></div></div>
</div>

<section class="abs updates">
  <h3>Stay In Touch&nbsp; with Our Updates</h3>
  <div class="field" style="top:69px">Enter First Name</div>
  <div class="field" style="top:109px">Enter Email Address</div>
  <div class="go">SIGN UP</div>
</section>

<div class="abs partners-label">Partners</div>
<div class="abs partner-badge"><span></span></div>
<div class="abs copyright">2016@study-along.example. All Rights Reserved.</div>
<div class="abs social"><i></i><i></i><i></i><i></i><i></i><i></i><i></i></div>

</body>
</html>
```